Start up business, dog breeder. Needs logo design and website.

I am a start up business looking for a logo design and a website. Briarwood Hollow Pups is a breeder of goldendoodles and labradoodles for home and sport. We have a strong emphasis on hunting lines within our dogs and strive to breed healthy companions for the field and the home. These dogs are a cross between golden retrievers and poodles or Labrador retrievers and poodles (some multigenerational) and possess a strong hunt drive along with the desire to please. Some people can't tolerate shedding and dander, whether due to allergies or personal preference. That's one of the things that makes these dogs so versatile - they are all low to nonshedding and allergy friendly for most people. Combine that with the intelligence, loyalty, need to please, temperament and athletic ability, and you have an amazing pet. We are marketing to people that want a nonshedding pet, and also to people who want a hunting companion. It is important to reach both groups of buyers, but not to lean too much toward either one. (The dogs flush and retrieve for bird hunters - pheasant, dove, quail, duck, etc.) They are raised, bred and trained on our small farm in Golden Valley County, Beach North Dakota, where they have lots of room to run, exercise and train in the prairie lands. The term "adopt" a puppy is preferred over "buy" a puppy.

I have purchased the web address with a wordpress platform through host lark.com. I started the website using one of their templates but wasn't pleased with it - need something far more professional than I'm capable of putting together. I will need help publishing the site and brief instructions on how to change and update when I have litters for adoption. I have quite a bit of content (text) and photos put together to give an idea of what we'd like it to say....feel free to edit away! I am no writer by any means, but it will share the business concept at least.

My "style" isn't really defined for a web design, but I can tell you what I like based on how I decorate my home: I love rustic mixed with dressy/contemporary, to offset all the rough edges, if that's any help. Think pallet wood walls with a crystal chandelier. I use lots of wood, plants, and repurpose old stuff for new uses. Natural, organic, texture.

I have a friendnook page, but haven't done much with it yet. www.friendnook.com/briarwoodhollowpups

I have a professional photographer coming to take photos of all my breeding stock next month, but I attached some snapshot photos to use as placeholders for the time being. Also attached of photo of my husband and I as owners and operators of Briarwood Hollow Pups. Peter Alan Whitcombe, and Meredith Whitcombe

Target Market(s)

Allergy sufferers who need a low to non shedding dog
People looking to add a beautiful intelligent trainable house pet to their family
Bird and duck hunters who need a hunting companion

Industry/Entity Type

Marketing

Requirements
Must have
• 1. Adoption questionnaire for prospective buyers. Form details/fields attached. When the buyer clicks "submit" the form results should go to my email address
2. Coin vault option for deposits and final payments (we do not accept credit cards)
3. An "outdoorsy" feel. Natural. Organic.
4. We are marketing to people that want a nonshedding pet, and also to people who want a hunting companion. It is important to reach both groups of buyers, but not to lean too much toward either one.
Nice to have
• A rustic feel. Look at trelminkfieldpups.com
Some reference to our namesake/location. "Golden Valley" is the county we live in and is named so for the surrounding croplands. Think rolling fields of wheat, pheasants, wildlife, meadows, ponds, hunting.....
Should not have
• 1. Music
2. Nothing froo-froo or silly, nothing cartoonish
3. An example of what I don't like (very homemade looking, unprofessional, terrible layout, cartoony looking) http://www.fernicopups.net http://www.pawmerikanet.com

```html
<!DOCTYPE html>
<html lang="en">
<head>
<meta charset="utf-8">
<title>Briarwood Hollow Pups</title>
<link href="https://fonts.googleapis.com/css2?family=Montserrat:wght@400;600;700;800&family=Open+Sans:wght@300;400;600&display=swap" rel="stylesheet">
<style>
:root{
  --blue:#36a3cf;
  --title-blue:#3b8fbd;
  --orange:#f7920f;
  --orange-dark:#e07f05;
  --grey-bg:#f1f1f1;
  --text:#555;
  --heading-grey:#666;
  --line:#cfcfcf;
  --white:#fff;
}
*{box-sizing:border-box;margin:0;padding:0}
html,body{width:788px;height:1200px;overflow:hidden}
body{font-family:"Open Sans",Arial,sans-serif;color:var(--text);background:var(--white);position:relative}
section,header,footer{position:absolute;left:0;width:788px}
.abs{position:absolute}

/* header */
.site-header{top:0;height:76px;background:linear-gradient(#fafafa,#e9e9e9);border-bottom:1px solid #d8d8d8}
.brand{left:116px;top:24px;display:flex;align-items:center;gap:8px}
.brand-dot{width:26px;height:26px;border-radius:50%;background:var(--orange)}
.brand-name{font-family:"Montserrat",sans-serif;font-weight:700;font-size:14px;color:var(--title-blue);width:110px;line-height:1.1}
.search{left:525px;top:12px;width:147px;height:20px;border:1px solid #ccc;background:#f6f6f6;font-size:7px;color:#aaa;padding:5px 6px}
.search svg{position:absolute;right:5px;top:3px}
.search::after{content:"";position:absolute;right:24px;top:2px;bottom:2px;border-left:1px solid #d2d2d2}
.main-nav{left:296px;top:50px;display:flex;gap:11px;font-family:"Montserrat",sans-serif;font-size:9.4px;color:#555}
.main-nav .active{color:var(--title-blue);font-weight:700;position:relative}
.main-nav .active::before{content:"";position:absolute;left:-2px;right:-2px;top:-6px;border-top:1px solid var(--orange)}
.main-nav .active::after{content:"";position:absolute;left:50%;top:-8px;width:4px;height:4px;margin-left:-2px;border-radius:50%;background:var(--orange)}

/* hero */
.hero{top:77px;height:303px;background:var(--white);border-bottom:1px solid #ddd}
.hero-title{left:116px;top:72px;font-family:"Montserrat",sans-serif;font-weight:800;font-size:26px;color:var(--blue);letter-spacing:-.5px}
.hero-text{left:116px;top:108px;width:300px;font-size:11px;font-weight:300;line-height:16.8px;color:#555;letter-spacing:-.2px}
.btn{display:inline-block;background:var(--orange);color:var(--white);font-family:"Montserrat",sans-serif;font-weight:700;text-align:center;border-bottom:2px solid var(--orange-dark);letter-spacing:-.3px}
.hero-btn{left:116px;top:202px;width:102px;height:28px;line-height:27px;font-size:13.5px}
.hero-photo{left:400px;top:20px;width:300px;height:262px;border-radius:48% 52% 40% 45%;background:radial-gradient(ellipse at 55% 45%,#f3e7d2 0%,#ebdcc2 50%,#fff 72%)}
.slider-dots{left:637px;top:282px;display:flex;gap:3px}
.slider-dots span{width:10px;height:10px;border-radius:50%;background:var(--orange)}
.slider-dots span:first-child{background:var(--blue)}

/* section headings */
.section-title{left:116px;width:556px;text-align:center;font-family:"Montserrat",sans-serif;font-weight:400;font-size:20px;color:var(--title-blue);letter-spacing:-.5px}
.section-title span{background:inherit;padding:0 18px;position:relative;z-index:1}
.section-title::before{content:"";position:absolute;left:0;right:0;top:50%;border-top:1px solid var(--line)}

/* pets */
.pets{top:381px;height:237px;background:var(--grey-bg)}
.pets .section-title span{background:var(--grey-bg)}
.pets-intro{left:116px;width:556px;top:58px;text-align:center;font-size:8px;line-height:11px;color:#666}
.pet-card{top:104px;width:183px;height:112px;border:1px solid #c8c8c8;background:var(--white);padding:6px}
.pet-card .photo{width:100%;height:100%}
.pet-feature{background:var(--orange);border-color:#e08a1a;text-align:center;color:#333;padding:20px 10px 0}
.pet-feature h3{font-family:"Montserrat",sans-serif;font-weight:700;font-size:13.5px;color:var(--white);margin-bottom:4px}
.pet-feature p{font-size:7.8px;line-height:10.5px;color:#3a2a10}
.pet-feature .learn{display:inline-block;margin-top:8px;background:var(--white);color:#7a1e1e;font-family:"Montserrat",sans-serif;font-weight:700;font-size:7.8px;padding:5px 10px;letter-spacing:-.2px}

/* about */
.about{top:618px;height:206px;background:var(--white)}
.about-title{left:116px;top:28px;font-family:"Montserrat",sans-serif;font-weight:400;font-size:19px;color:var(--heading-grey);letter-spacing:-.5px;display:flex;align-items:center;gap:16px}
.about-title::after{content:"";width:84px;border-top:1px solid var(--line)}
.about-text{left:116px;top:60px;width:215px;font-size:8.6px;line-height:13.5px;color:#555}
.about-btn{left:116px;top:163px;width:74px;height:22px;line-height:21px;font-size:10px}
.dog-form{left:346px;top:19px;width:326px;height:165px;background:var(--blue);border:1px solid #2f93bb;color:var(--white)}
.dog-form h2{position:absolute;left:0;right:0;top:10px;text-align:center;font-family:"Montserrat",sans-serif;font-weight:700;font-size:14px;letter-spacing:-.4px}
.field{position:absolute;width:140px;font-family:"Montserrat",sans-serif;font-size:6.8px;font-weight:600;text-transform:uppercase}
.field span{display:block;margin-bottom:3px}
.field i{display:block;height:18px;background:var(--white);border:1px solid #d6e8f0}
.form-submit{left:131px;top:127px;width:74px;height:23px;line-height:22px;font-size:11px}

/* puppies */
.puppies{top:824px;height:216px;background:var(--grey-bg)}
.puppies .section-title{top:13px}
.puppies .section-title span{background:var(--grey-bg)}
.puppies-intro{left:116px;width:556px;top:42px;text-align:center;font-size:11px;color:#555}
.puppy{top:71px;width:183px}
.puppy .frame{height:111px;border:1px solid #c8c8c8;background:var(--white);padding:1px}
.puppy .frame div{width:100%;height:100%}
.puppy a{display:block;margin-top:6px;font-family:"Montserrat",sans-serif;font-size:10.5px;color:var(--blue);text-decoration:none}

/* footer */
.site-footer{top:1040px;height:136px;background:var(--orange);color:var(--white)}
.foot-col{top:26px}
.foot-col h4{font-family:"Montserrat",sans-serif;font-weight:700;font-size:10.2px;margin-bottom:6px}
.foot-col li{list-style:none;font-size:7.8px;line-height:14.5px}
.foot-col p{font-size:7.8px;line-height:11.5px}
.foot-divider{top:24px;height:96px;border-left:1px solid rgba(255,255,255,.25)}
.social{left:570px;top:35px;display:flex;gap:6px}
.social span{width:21px;height:21px;border-radius:50%;background:rgba(255,255,255,.35)}
.foot-brand{left:572px;top:80px;display:flex;align-items:center;gap:7px}
.foot-brand .brand-dot{background:rgba(255,255,255,.9);width:22px;height:22px}
.foot-brand .brand-name{color:var(--white);font-size:10px;width:90px}
.copyright{left:0;width:788px;top:1176px;height:24px;background:var(--blue);color:var(--white);font-size:7.8px;padding:6px 0 0 116px}
</style>
</head>
<body>

<header class="site-header">
  <div class="brand abs"><span class="brand-dot"></span><span class="brand-name">Briarwood Hollow Pups</span></div>
  <div class="search abs">Search Types of Dogs
    <svg width="12" height="12" viewBox="0 0 12 12"><circle cx="5" cy="5" r="3.6" fill="none" stroke="#999" stroke-width="1.2"/><line x1="7.6" y1="7.6" x2="11" y2="11" stroke="#999" stroke-width="1.4"/></svg>
  </div>
  <nav class="main-nav abs">
    <span class="active">Home</span><span>Our Dogs</span><span>Breeding</span><span>Available</span><span>Resources</span><span>Gallery</span><span>Past Puppies</span><span>Contact</span>
  </nav>
</header>

<section class="hero">
  <h1 class="hero-title abs">GOLDEN DOODLES</h1>
  <p class="hero-text abs">Hunting dog breeds such as Labrador retrievers still maintain their hunting instincts, even if they never go hunting in their lives. You can stimulate their hunter's nature and help train them to hunt by providing them with interactive toys that will curb boredom.</p>
  <a class="btn hero-btn abs">READ MORE</a>
  <div class="hero-photo abs" role="img" aria-label="Photo of a cream goldendoodle lying down on a white background"></div>
  <div class="slider-dots abs"><span></span><span></span><span></span></div>
</section>

<section class="pets">
  <h2 class="section-title abs" style="top:30px"><span>OUR PETS</span></h2>
  <p class="pets-intro abs">Lorem Ipsum is simply dummy text of the printing and typesetting industry. Lorem Ipsum has been the industry's standard dummy text ever since the 1500s, when an unknown printer took a galley of typ e and scrambled it to make a type specimen book.</p>
  <div class="pet-card abs" style="left:116px"><div class="photo" role="img" aria-label="Photo of a sitting cream doodle puppy" style="background:radial-gradient(ellipse at 50% 55%,#efdcbd 0%,#f7eddc 35%,#fff 60%)"></div></div>
  <div class="pet-card pet-feature abs" style="left:302px">
    <h3>LABRADOODLES</h3>
    <p>Lorem Ipsum is simply dummy text of the printing and typesetting industry.</p>
    <span class="learn">LEARN MORE ABOUT THIS PET</span>
  </div>
  <div class="pet-card abs" style="left:490px"><div class="photo" role="img" aria-label="Photo of a cream doodle resting on a patterned dog bed" style="background:radial-gradient(ellipse at 50% 70%,#b39a76 0%,#e9dcc8 40%,#fff 65%)"></div></div>
</section>

<section class="about">
  <h2 class="about-title abs">ABOUT US</h2>
  <p class="about-text abs">Lorem Ipsum is simply dummy text of the printing and typesetting industry. Lorem Ipsum has been the industry's standard dummy text ever since the 1500s, when an unknown printer took a galley of type and scrambled it to make a type specimen book. It has survived not only five centuries, but remaining essentially unchanged.</p>
  <a class="btn about-btn abs">READ MORE</a>
  <form class="dog-form abs">
    <h2>SELECTING PERFECT DOG</h2>
    <label class="field" style="left:16px;top:46px"><span>Name</span><i></i></label>
    <label class="field" style="left:173px;top:46px"><span>Email Address</span><i></i></label>
    <label class="field" style="left:16px;top:90px"><span>City/Area</span><i></i></label>
    <label class="field" style="left:173px;top:90px"><span>What type of dogs you like?</span><i></i></label>
    <a class="btn form-submit abs">SUBMIT</a>
  </form>
</section>

<section class="puppies">
  <h2 class="section-title abs"><span>OUR PUPPIES</span></h2>
  <p class="puppies-intro abs">Lorem Ipsum is simply dummy text of the printing and typesetting industry.</p>
  <div class="puppy abs" style="left:116px"><div class="frame"><div role="img" aria-label="Photo of a cream doodle sitting in a green field" style="background:linear-gradient(#c9c4b0 0%,#a7a27e 30%,#5d7a3a 45%,#6f8e45 100%)"></div></div><a>Hunting Companion</a></div>
  <div class="puppy abs" style="left:303px"><div class="frame"><div role="img" aria-label="Photo of a brown doodle puppy on a white background" style="background:radial-gradient(ellipse at 50% 55%,#6b3a26 0%,#8d5a44 28%,#fff 55%)"></div></div><a>House Pet</a></div>
  <div class="puppy abs" style="left:490px"><div class="frame"><div role="img" aria-label="Photo of a man in a brown jacket with a cream doodle outdoors" style="background:linear-gradient(100deg,#6d4b2c 0%,#8a5c34 45%,#b7a68a 70%,#d8d2c4 100%)"></div></div><a>Allergy Sufferers</a></div>
</section>

<footer class="site-footer">
  <div class="foot-col abs" style="left:116px"><h4>Links</h4><ul><li>Home</li><li>Our Dogs</li><li>Breeding</li><li>Available</li><li>Past Puppies</li><li>Contact</li></ul></div>
  <div class="foot-divider abs" style="left:212px"></div>
  <div class="foot-col abs" style="left:242px"><h4>About Us</h4><ul><li>FAQ</li><li>Contact Us</li><li>Privacy Policy</li><li>Site Map</li></ul></div>
  <div class="foot-divider abs" style="left:344px"></div>
  <div class="foot-col abs" style="left:377px;width:150px"><h4>Contact us</h4><p>Phone No: 1-555-010-2991<br>Email: info@briarwoodhollowpups.com.au<br>Our Location</p></div>
  <div class="foot-divider abs" style="left:542px"></div>
  <div class="social abs"><span></span><span></span><span></span><span></span></div>
  <div class="foot-brand abs"><span class="brand-dot"></span><span class="brand-name">Briarwood Hollow Pups</span></div>
</footer>
<div class="copyright abs">© copyright 2013 Briarwood Hollow Pups. All right Reserved.</div>

</body>
</html>
```